Redesign of business card for Cedar Ridge Mechanical

We are looking for a new design for our business cards for Cedar Ridge Mechanical. We are a plumbing & HVAC construction company, operating on the West Coast of Canada and USA. Logo attached.
Industry/Entity Type
Construction - Plumbing & HVAC
Contact Information for Business Card
Name, address, phone numbers, email, website address
Look and feel
Each slider illustrates characteristics of the customer's brand and the style your logo design should communicate.

```html
<!DOCTYPE html>
<html lang="en">
<head>
<meta charset="utf-8">
<title>Cedar Ridge Mechanical – Business Card</title>
<link href="https://fonts.googleapis.com/css2?family=Montserrat:wght@400;700&family=Oswald:wght@500&display=swap" rel="stylesheet">
<style>
  :root {
    --backdrop: #2a2a2c;
    --card-dark: #1c1c1c;
    --card-black: #0e0e0e;
    --paper: #ffffff;
    --band-grey: #9a9a9a;
    --ink-light: #f2f2f2;
    --ink-dark: #151515;
  }
  * { margin: 0; padding: 0; box-sizing: border-box; }
  html, body {
    width: 1200px; height: 801px; overflow: hidden;
    background: var(--backdrop);
  }
  .stage {
    position: relative; width: 1200px; height: 801px;
    display: flex; align-items: center; justify-content: center; gap: 60px;
  }
  .card {
    position: relative; width: 520px; height: 300px;
    border-radius: 18px; overflow: hidden;
    box-shadow: 0 14px 30px rgba(0,0,0,.45);
  }
  /* Front */
  .card-front { background: var(--card-dark); }
  .contact-panel {
    position: absolute; left: 34px; top: 0; bottom: 0; width: 230px;
    display: flex; flex-direction: column; justify-content: center;
    font-family: 'Montserrat', sans-serif; color: var(--ink-light);
  }
  .person-name { font-weight: 700; font-size: 18px; letter-spacing: .5px; }
  .person-role { font-size: 14px; margin-bottom: 22px; }
  .address { font-size: 14px; line-height: 1.3; margin-bottom: 22px; }
  .contact-line { display: flex; align-items: center; gap: 8px; font-size: 14px; line-height: 1.45; }
  .contact-line svg { width: 11px; height: 11px; flex: none; }
  .brand-panel {
    position: absolute; right: 0; top: 0; bottom: 0; width: 262px;
  }
  .brand-band {
    position: absolute; right: 0; width: 16px; background: var(--band-grey);
  }
  .brand-band.top { top: 0; height: 44px; }
  .brand-band.bottom { bottom: 0; height: 44px; }
  .brand-tile {
    position: absolute; left: 0; right: 16px; top: 0; bottom: 0;
    background: var(--paper); border-radius: 0 0 0 18px;
    display: flex; align-items: center; justify-content: center; gap: 10px;
  }
  .brand-mark { width: 14px; height: 14px; background: var(--ink-dark); }
  .brand-name {
    font-family: 'Oswald', sans-serif; font-weight: 500; font-size: 19px;
    letter-spacing: 1px; color: var(--ink-dark); text-transform: uppercase;
  }
  /* Back */
  .card-back { background: var(--card-black); display: flex; align-items: center; justify-content: center; }
  .back-title {
    font-family: 'Oswald', sans-serif; font-weight: 500; font-size: 36px;
    letter-spacing: 2px; color: var(--ink-light); text-transform: uppercase;
  }
</style>
</head>
<body>
<main class="stage">
  <section class="card card-front">
    <div class="contact-panel">
      <p class="person-name">DANIEL HUGHES</p>
      <p class="person-role">Manager</p>
      <p class="address">Your address, city<br>state, ZIP 0000</p>
      <p class="contact-line">
        <svg viewBox="0 0 12 12"><path d="M3 1 L5 3.5 L4 5 Q5.5 7 7 8 L8.5 7 L11 9 L10 11 Q5 11 1 2 Z" fill="#f2f2f2"/></svg>
        123-456-2100
      </p>
      <p class="contact-line">
        <svg viewBox="0 0 12 12"><rect x="1" y="2.5" width="10" height="7" rx="1" fill="#f2f2f2"/><path d="M1.5 3 L6 6.5 L10.5 3" stroke="#1c1c1c" fill="none"/></svg>
        youremail@mailbox.com
      </p>
      <p class="contact-line">
        <svg viewBox="0 0 12 12"><circle cx="6" cy="6" r="5" fill="#f2f2f2"/><path d="M1 6 H11 M6 1 Q3 6 6 11 Q9 6 6 1" stroke="#1c1c1c" fill="none" stroke-width=".8"/></svg>
        www.yourwebsite.com
      </p>
    </div>
    <div class="brand-panel">
      <div class="brand-band top"></div>
      <div class="brand-band bottom"></div>
      <div class="brand-tile">
        <span class="brand-mark"></span>
        <span class="brand-name">Cedar Ridge Mechanical</span>
      </div>
    </div>
  </section>
  <section class="card card-back">
    <h1 class="back-title">Cedar Ridge Mechanical</h1>
  </section>
</main>
</body>
</html>
```